Modern Business Card for Larkwell 2018

Our company assumes the best about people. We are creating an online community of entrepreneurs and business leaders who struggle with marketing their business online.

This business card should POP! We recently got a new logo and are launching a new website next month, so our business cards should make a statement that feels:
-Fresh
-Smart
-Trustworthy
-Fun

Target Market(s)

small business owners, entrepreneurs

Industry/Entity Type

Digital Marketing

Contact Information for Business Card

Dimensions: 3.5" x 2"

Font styles to use
Sans Serif

Colors
f37122
ffffff

Requirements
Must have
• We need a business card with a modern, bold design. We will use one side of the card as a lead-generation offer, so text on one side will need to fit up to 140 characters. The business card should stick to our core colors (orange, black, and white).
Nice to have
• We think a vertical "portrait" design could be interesting.
Should not have
• Should not look like a traditional business card. The round icon should stand out from a distance.

```html
<!DOCTYPE html>
<html lang="en">
<head>
<meta charset="utf-8">
<title>Larkwell Business Card</title>
<link rel="stylesheet" href="https://fonts.googleapis.com/css2?family=Roboto:wght@400;700;900&family=Roboto+Condensed:wght@400;700&display=swap">
<style>
  :root {
    --orange: #f26a25;
    --white: #ffffff;
    --paper: #f3f3f3;
    --backdrop: #262626;
    --rule: #3a3a3a;
  }
  * { margin: 0; padding: 0; box-sizing: border-box; }
  html, body {
    width: 1200px;
    height: 960px;
    overflow: hidden;
    background: var(--backdrop);
    font-family: "Roboto", Arial, sans-serif;
  }
  .canvas { position: relative; width: 1200px; height: 960px; }
  .card {
    position: absolute;
    width: 600px;
    height: 343px;
    background: var(--paper);
    overflow: hidden;
  }
  .card--front { left: 314px; top: 113px; }
  .card--back { left: 311px; top: 472px; }

  .band { position: absolute; left: 0; width: 100%; background: var(--orange); color: var(--white); }
  .card--front .band { top: 92px; height: 160px; }
  .card--back .band { top: 0; height: 218px; }

  .divider { position: absolute; width: 1px; background: rgba(255,255,255,0.85); }
  .card--front .divider { left: 262px; top: 7px; height: 146px; }
  .card--back .divider { left: 298px; top: 26px; height: 168px; }

  .brand-disc {
    position: absolute;
    left: 89px; top: 8px;
    width: 144px; height: 144px;
    border-radius: 50%;
    background: var(--white);
    display: flex; align-items: center; justify-content: center;
  }
  .brand-disc__name {
    font-weight: 900;
    font-size: 21px;
    letter-spacing: 0.5px;
    color: var(--orange);
    text-transform: uppercase;
  }

  .contact { position: absolute; left: 295px; top: 46px; }
  .contact__name {
    font-family: "Roboto Condensed", Arial, sans-serif;
    font-weight: 700; font-size: 24px; line-height: 28px;
    text-transform: uppercase;
  }
  .contact__role {
    font-size: 15px; line-height: 20px;
    text-transform: uppercase;
  }
  .contact__email { font-size: 14px; line-height: 18px; }

  .lockup { position: absolute; left: 43px; top: 58px; width: 234px; text-align: center; }
  .lockup__dot {
    display: block; margin: 0 auto 14px;
    width: 38px; height: 38px; border-radius: 50%;
    background: var(--white);
  }
  .lockup__name {
    font-weight: 900; font-size: 40px; line-height: 36px;
    letter-spacing: 2.5px; text-transform: uppercase;
  }
  .lockup__tagline {
    margin-top: 8px;
    font-family: "Roboto Condensed", Arial, sans-serif;
    font-weight: 700; font-size: 12px; letter-spacing: 0.6px;
    text-transform: uppercase;
  }

  .offer { position: absolute; left: 323px; top: 30px; }
  .offer__headline {
    font-weight: 700; font-size: 19.5px; line-height: 21.5px;
    text-transform: uppercase;
  }
  .offer__body { margin-top: 4px; font-size: 15px; line-height: 19.5px; }
  .offer__url { margin-top: 11px; font-weight: 700; font-size: 20px; line-height: 22px; }

  .note-lines { position: absolute; left: 36px; top: 260px; width: 520px; }
  .note-line { height: 1px; background: var(--rule); margin-bottom: 39px; }
</style>
</head>
<body>
<main class="canvas">
  <section class="card card--front" aria-label="Card front">
    <div class="band">
      <div class="brand-disc"><span class="brand-disc__name">Larkwell</span></div>
      <div class="divider"></div>
      <div class="contact">
        <p class="contact__name">Dana Whitlock</p>
        <p class="contact__role">Story Marketing Coach</p>
        <p class="contact__email">dana@larkwellnow.com</p>
      </div>
    </div>
  </section>

  <section class="card card--back" aria-label="Card back">
    <div class="band">
      <div class="lockup">
        <span class="lockup__dot"></span>
        <p class="lockup__name">Larkwell</p>
        <p class="lockup__tagline">Share ideas that spark growth</p>
      </div>
      <div class="divider"></div>
      <div class="offer">
        <p class="offer__headline">Reach more people.<br>Make more money.<br>Create more impact.</p>
        <p class="offer__body">Get your free Larkwell<br>Starter Package and our<br>marketing guide today at</p>
        <p class="offer__url">Larkwellnow.com/start</p>
      </div>
    </div>
    <div class="note-lines">
      <div class="note-line"></div>
      <div class="note-line"></div>
    </div>
  </section>
</main>
</body>
</html>
```